Corportate Power Point Template

We need a corporate PPT Design for our startup Big Data company.

Basically, our company will ingest, analyze and generate dynamic Dashboards with data consumed from different sources like Social Networks, Enterprise Legacy Systems such as e-Commerce, ERP, CRM and others.

Company is headquartered in Brazil, but will have a global presence.

Industry/Entity Type

It Company

```html
<!DOCTYPE html>
<html lang="en">
<head>
<meta charset="utf-8">
<title>Project Title Here</title>
<link href="https://fonts.googleapis.com/css2?family=Open+Sans:wght@400;600&family=Titillium+Web:wght@400&display=swap" rel="stylesheet">
<style>
  :root {
    --slide-bg: #efedee;
    --footer-bg: #ffffff;
    --ink: #333333;
    --ink-soft: #444444;
    --title-red: #e8352a;
    --title-grey: #7a7a7a;
    --accent-bar: #000000;
    --rule: #b5b5b5;
    --axis: #333333;
    --bar-grey: #8c8c8c;
    --bar-dark: #6f6f6f;
    --bar-red: #ee3124;
    --bar-coral: #fe5f55;
    --bar-salmon: #ff7a70;
    --bar-pink: #ffaaa5;
  }
  html, body {
    margin: 0;
    padding: 0;
    overflow: hidden;
  }
  .slide {
    position: relative;
    width: 1200px;
    height: 900px;
    background: var(--slide-bg);
    overflow: hidden;
    font-family: "Open Sans", Arial, sans-serif;
    color: var(--ink);
  }
  .title-marker {
    position: absolute;
    left: 0;
    top: 31px;
    width: 15px;
    height: 66px;
    background: var(--accent-bar);
  }
  .slide-title {
    position: absolute;
    left: 26px;
    top: 24px;
    margin: 0;
    font-family: "Titillium Web", "Arial Narrow", sans-serif;
    font-weight: 400;
    font-size: 58px;
    line-height: 80px;
    letter-spacing: 0.3px;
    color: var(--title-grey);
    white-space: nowrap;
  }
  .slide-title .highlight { color: var(--title-red); }
  .slide-subtitle {
    position: absolute;
    left: 63px;
    top: 134px;
    margin: 0;
    font-weight: 600;
    font-size: 21px;
    line-height: 32px;
    color: var(--ink);
    white-space: nowrap;
  }
  .chart {
    position: absolute;
    left: 0;
    top: 0;
    width: 1200px;
    height: 900px;
  }
  .y-label, .x-label {
    position: absolute;
    font-size: 18px;
    line-height: 24px;
    color: var(--ink-soft);
    white-space: nowrap;
  }
  .y-label {
    right: 951px;
    transform: translateY(-50%);
  }
  .x-label {
    top: 698px;
  }
  .footer {
    position: absolute;
    left: 0;
    top: 807px;
    width: 1200px;
    height: 93px;
    background: var(--footer-bg);
    border-top: 2px solid var(--rule);
    box-sizing: border-box;
  }
  .brand {
    position: absolute;
    left: 18px;
    top: 50%;
    transform: translateY(-50%);
    font-family: "Open Sans", Arial, sans-serif;
    font-weight: 400;
    font-size: 34px;
    color: var(--ink);
    white-space: nowrap;
  }
  .copyright {
    position: absolute;
    right: 15px;
    top: 50%;
    transform: translateY(-50%);
    font-family: "Titillium Web", "Arial Narrow", sans-serif;
    font-size: 23px;
    color: var(--ink);
    white-space: nowrap;
  }
</style>
</head>
<body>
<main class="slide">
  <div class="title-marker"></div>
  <h1 class="slide-title"><span class="highlight">PROJECT</span> TITLE HERE</h1>
  <p class="slide-subtitle">Lorem ipsum dolor sit ipsum Lorem ipsum dolor sit ipsum Lorem ipsum Lorem ipsum</p>

  <svg class="chart" viewBox="0 0 1200 900" aria-label="Bar chart">
    <rect x="262.5" y="532.5" width="49.5" height="144.5" fill="var(--bar-grey)"/>
    <rect x="325.5" y="420" width="61.5" height="257" fill="var(--bar-red)"/>
    <rect x="402" y="465" width="60" height="212" fill="var(--bar-coral)"/>
    <rect x="475.5" y="549" width="60" height="128" fill="var(--bar-salmon)"/>
    <rect x="553.5" y="639" width="66" height="38" fill="var(--bar-pink)"/>
    <rect x="631.5" y="663" width="75" height="14" fill="var(--bar-dark)"/>
    <rect x="717" y="274.5" width="60" height="402.5" fill="var(--bar-red)"/>
    <rect x="790.5" y="636" width="66" height="41" fill="var(--bar-coral)"/>
    <rect x="868.5" y="657" width="64.5" height="20" fill="var(--bar-coral)"/>
    <line x1="263" y1="235" x2="263" y2="677" stroke="var(--axis)" stroke-width="1.5"/>
    <line x1="262" y1="677" x2="1022" y2="677" stroke="var(--axis)" stroke-width="1.5"/>
  </svg>

  <span class="y-label" style="top:261px">Lorem ipsum text here</span>
  <span class="y-label" style="top:330px">Lorem ipsum text here</span>
  <span class="y-label" style="top:423px">Lorem ipsum text here</span>
  <span class="y-label" style="top:537px">Lorem ipsum text here</span>
  <span class="y-label" style="top:670px">Lorem ipsum text here</span>

  <span class="x-label" style="left:261px">Lorem ipsum text here</span>
  <span class="x-label" style="left:522px">Lorem ipsum text here</span>
  <span class="x-label" style="left:838px">Lorem ipsum text here</span>

  <footer class="footer">
    <div class="brand">Quarrystone Data</div>
    <div class="copyright">Copyright text here</div>
  </footer>
</main>
</body>
</html>
```